New Business Card Design

We need a business card design for a new company based in Sydney called "Haven and Hue". This is an online buisness which will have an online store providing imported homewares.
We are looking for something that is different, perhaps even in shape and using the logo that was designed by Pixel Harbor.

Attached document is a basic example I want to see more creative versions.

Target Market(s)

Homewares, Interior Design

Industry/Entity Type

Business

Contact Information for Business Card

Company Logo
Company Name
Industry area
Name
Position
Phone
Email
Website
Motto

Requirements
Must have
• Logo
Nice to have
• Social website logos - Chatterloop, Glimmoraly, Quibbly, Boardlyne, Veltrix+

```html
<!DOCTYPE html>
<html lang="en">
<head>
<meta charset="utf-8">
<title>Haven and Hue – Business Card</title>
<link href="https://fonts.googleapis.com/css2?family=Lato:wght@400;700;900&display=swap" rel="stylesheet">
<style>
  :root {
    --backdrop: #bdbdbd;
    --card: #ffffff;
    --ink: #1a1a1a;
    --gold: #b5832a;
    --dark: #111111;
  }
  html, body {
    margin: 0;
    padding: 0;
    width: 1200px;
    height: 1000px;
    overflow: hidden;
    background: var(--backdrop);
    font-family: "Lato", sans-serif;
  }
  .canvas {
    position: relative;
    width: 1200px;
    height: 1000px;
  }
  .card {
    position: absolute;
    width: 700px;
    height: 400px;
    background: var(--card);
    border-radius: 22px;
    box-shadow: 0 6px 14px rgba(0,0,0,0.25);
  }
  .card-front { left: 70px; top: 60px; }
  .card-back  { left: 430px; top: 540px; }

  .brand-mark {
    position: absolute;
    display: flex;
    align-items: center;
    gap: 12px;
  }
  .brand-mark .dot {
    width: 22px;
    height: 22px;
    border-radius: 50%;
    background: var(--gold);
  }
  .brand-mark .brand-name {
    font-size: 40px;
    font-weight: 900;
    color: var(--dark);
    white-space: nowrap;
  }
  .card-front .brand-mark { left: 50%; top: 50%; transform: translate(-50%, -50%); }
  .card-back .brand-mark { left: 40px; top: 50%; transform: translateY(-50%); }
  .card-back .brand-mark .brand-name { font-size: 34px; }

  .social-row {
    position: absolute;
    top: 28px;
    right: 30px;
    display: flex;
    gap: 12px;
  }
  .social-item {
    display: flex;
    align-items: center;
    gap: 4px;
    font-size: 11px;
    font-weight: 700;
    color: var(--dark);
  }
  .social-item .dot {
    width: 12px;
    height: 12px;
    border-radius: 50%;
    background: var(--dark);
  }

  .divider {
    position: absolute;
    left: 330px;
    top: 60px;
    width: 2px;
    height: 280px;
    background: var(--gold);
  }
  .contact {
    position: absolute;
    left: 355px;
    top: 62px;
    color: var(--ink);
  }
  .person-name {
    margin: 0;
    font-size: 30px;
    font-weight: 900;
    color: var(--gold);
    line-height: 1.1;
  }
  .person-role {
    margin: 2px 0 26px 0;
    font-size: 24px;
    font-weight: 400;
  }
  .contact-list {
    list-style: none;
    margin: 0;
    padding: 0;
    font-size: 19px;
    line-height: 1.45;
  }
  .contact-list li {
    display: flex;
    align-items: center;
    gap: 10px;
  }
  .contact-list svg { width: 18px; height: 18px; flex: none; }
  .address {
    margin-top: 26px;
    display: flex;
    align-items: flex-start;
    gap: 10px;
    font-size: 19px;
    line-height: 1.3;
  }
  .address svg { width: 18px; height: 24px; flex: none; margin-top: 4px; }
</style>
</head>
<body>
<div class="canvas">

  <section class="card card-front" aria-label="Card front">
    <div class="social-row">
      <span class="social-item"><span class="dot"></span>Chatterloop</span>
      <span class="social-item"><span class="dot"></span>Quibbly</span>
      <span class="social-item"><span class="dot"></span>Glimmoraly</span>
      <span class="social-item"><span class="dot"></span>Boardlyne</span>
      <span class="social-item"><span class="dot"></span>Veltrix+</span>
    </div>
    <div class="brand-mark">
      <span class="dot"></span>
      <span class="brand-name">Haven and Hue</span>
    </div>
  </section>

  <section class="card card-back" aria-label="Card back">
    <div class="brand-mark">
      <span class="brand-name">Haven and Hue</span>
    </div>
    <div class="divider"></div>
    <div class="contact">
      <h1 class="person-name">Marcus Ellery</h1>
      <p class="person-role">Director</p>
      <ul class="contact-list">
        <li>
          <svg viewBox="0 0 24 24"><path fill="#b5832a" d="M6.6 10.8a15 15 0 0 0 6.6 6.6l2.2-2.2a1 1 0 0 1 1-.25 11.4 11.4 0 0 0 3.6.57 1 1 0 0 1 1 1V20a1 1 0 0 1-1 1A17 17 0 0 1 3 4a1 1 0 0 1 1-1h3.5a1 1 0 0 1 1 1c0 1.25.2 2.45.57 3.6a1 1 0 0 1-.25 1z"/></svg>
          02 5550 1987
        </li>
        <li>
          <svg viewBox="0 0 24 24"><rect x="2" y="5" width="20" height="14" rx="1" fill="#b5832a"/><path d="M2 6l10 7 10-7" fill="none" stroke="#fff" stroke-width="1.6"/></svg>
          me@havenandhue.com.au
        </li>
        <li>
          <svg viewBox="0 0 24 24"><g fill="none" stroke="#b5832a" stroke-width="1.8"><circle cx="12" cy="12" r="9.5"/><ellipse cx="12" cy="12" rx="4.5" ry="9.5"/><path d="M2.5 12h19M4 7h16M4 17h16"/></g></svg>
          www.havenandhue.com.au
        </li>
      </ul>
      <div class="address">
        <svg viewBox="0 0 18 24"><path fill="#b5832a" d="M9 0a8 8 0 0 0-8 8c0 6 8 16 8 16s8-10 8-16a8 8 0 0 0-8-8zm0 11a3 3 0 1 1 0-6 3 3 0 0 1 0 6z"/></svg>
        <span>Unit 4, Lantern Avenue<br>Marrowick 2150 NSW AU</span>
      </div>
    </div>
  </section>

</div>
</body>
</html>
```